Infoblatt
Zielgruppe
Talentförderung, Personalentwicklung, Beratung von Personalabteilungen
Zielgruppe: Personaler, HR Verantwortliche
Aufgabenstellung
Es geht um einen "One-Pager", der auf einem Kongress ausgelegt werden soll und in Kurzform einen Überblick über unser Unternehmen und unser Angebot informieren soll.
Wir haben Visitenkarten auf Recyclingpapier und möchten das Blatt konsistent auf das gleiche Papier drucken lassen, daher einfarbig schwarz. Format DIN A4 Hoch.
IDEE: Vom Stil wie eine Infografik aufbauen
TYPO: unser LOGO ist BEBAS NEUE und unsere Schrift Helvetica

```html
<!DOCTYPE html>
<html lang="de">
<head>
<meta charset="utf-8">
<title>Tugendhaus – Talent und Talentförderung</title>
<link href="https://fonts.googleapis.com/css2?family=Bebas+Neue&family=Arimo:wght@400;700&display=swap" rel="stylesheet">
<style>
  :root {
    --ink: #000000;
    --text: #2a2a2a;
    --paper: #ffffff;
    --photo-light: #e9e9e9;
    --photo-dark: #8c8c8c;
    --tint-1: #e2e6e2;
    --tint-2: #c9cfca;
    --tint-3: #6a7472;
    --tint-4: #56605e;
    --tint-5: #7e8781;
  }
  html, body {
    margin: 0;
    padding: 0;
    width: 848px;
    height: 1200px;
    overflow: hidden;
    background: var(--paper);
  }
  .sheet {
    position: relative;
    width: 848px;
    height: 1200px;
    overflow: hidden;
    background: var(--paper);
    font-family: "Arimo", "Helvetica Neue", Helvetica, Arial, sans-serif;
    color: var(--text);
  }
  .hero-photo {
    position: absolute;
    left: 0; top: 0;
    width: 848px; height: 495px;
    background: linear-gradient(160deg, #b9b9b9 0%, #d7d7d7 30%, var(--photo-light) 55%, #f5f5f5 70%, #a9a9a9 100%);
  }
  .backdrop {
    position: absolute;
    left: 0; top: 0;
    width: 848px; height: 1200px;
  }
  .brand {
    position: absolute;
    left: 52px; top: 44px;
    margin: 0;
    font-family: "Bebas Neue", "Arimo", sans-serif;
    font-weight: 400;
    font-size: 96px;
    line-height: 1;
    letter-spacing: 0.5px;
    color: var(--ink);
  }
  .tagline {
    position: absolute;
    left: 52px; top: 147px;
    margin: 0;
    padding-bottom: 5px;
    border-bottom: 2px solid var(--ink);
    font-weight: 700;
    font-size: 22.5px;
    letter-spacing: 2.2px;
    line-height: 1.1;
    color: var(--ink);
  }
  .section-title {
    position: absolute;
    left: 283px;
    margin: 0;
    padding: 3px 7px 2px;
    background: var(--ink);
    color: var(--paper);
    font-weight: 700;
    font-size: 18px;
    letter-spacing: 1.6px;
    line-height: 21px;
  }
  .copy {
    position: absolute;
    left: 283px;
    width: 530px;
    margin: 0;
    font-size: 14.6px;
    line-height: 20.2px;
    color: var(--text);
  }
  .offer-group { position: absolute; left: 283px; margin: 0; }
  .offer-group h3 {
    margin: 0;
    font-size: 14.6px;
    font-weight: 700;
    line-height: 20.4px;
    color: var(--ink);
  }
  .offer-group ul {
    margin: 0;
    padding: 0;
    list-style: none;
    font-size: 14.6px;
    line-height: 20.4px;
  }
  .offer-group li { padding-left: 16px; position: relative; }
  .offer-group li::before {
    content: "";
    position: absolute;
    left: 3px; top: 8px;
    width: 5px; height: 5px;
    border-radius: 50%;
    background: var(--ink);
  }
</style>
</head>
<body>
<div class="sheet">
  <div class="hero-photo" role="img" aria-label="Schwarzweißfoto: Flipchartpapier mit Notizen und ein Stift auf einem Holztisch"></div>

  <svg class="backdrop" viewBox="0 0 848 1200" aria-hidden="true">
    <polygon points="0,0 591,591 0,1182" fill="var(--tint-1)" opacity="0.72"/>
    <polygon points="0,570 258,828 0,1086" fill="var(--tint-2)"/>
    <polygon points="0,336 180,516 0,696" fill="var(--tint-3)"/>
    <polygon points="0,540 78,618 0,700" fill="var(--tint-4)"/>
    <polygon points="0,846 51,897 0,948" fill="var(--tint-5)"/>
  </svg>

  <h1 class="brand">Tugendhaus</h1>
  <p class="tagline">TALENT UND TALENTFÖRDERUNG</p>

  <h2 class="section-title" style="top:555px;">WORAN WIR GLAUBEN</h2>
  <p class="copy" style="top:596px;">Wir glauben, dass sich persönliche und ökonomische Werte ergänzen -<br>mehr noch, dass sie langfristig nicht ohne einander auskommen und<br>dass sich emotionale Bindung als Mehrwert in Zahlen ausdrückt.</p>

  <h2 class="section-title" style="top:689px;">WAS WIR BIETEN</h2>
  <p class="copy" style="top:730px;">Wir beraten Unternehmen im Rahmen der Talentförderung und helfen<br>Jugendlichen auf dem Weg in ihr Berufsleben.</p>

  <div class="offer-group" style="top:791px;">
    <h3>Für Unternehmen</h3>
    <ul>
      <li>Talentförderung &amp; Talent Management</li>
      <li>Professionalisierung der Personalarbeit</li>
      <li>Organisationsentwicklung</li>
      <li>Potentialorientierte Mitarbeiterführung</li>
    </ul>
  </div>

  <div class="offer-group" style="top:911px;">
    <h3>Für die junge Generation</h3>
    <ul>
      <li>Berufsorientierung</li>
      <li>Bewerbungscoaching</li>
    </ul>
  </div>

  <h2 class="section-title" style="top:1008px;">WAS UNSER HANDELN LEITET</h2>
  <p class="copy" style="top:1046px;">Kundare heißt marktschreierisch anpreisen, hinters Licht führen, täuschen.<br>Mandare heißt beauftragen, Vertrauen schenken. Wir legen großen Wert<br>auf eine Beziehung, die Mandare, nicht Kundare entspricht. Für uns ist<br>der partnerschaftliche Umgang mit unseren Mandanten das Fundament.<br>Wir haben keine Kunden. Wir unterstützen Mandanten.</p>
</div>
</body>
</html>
```